Business Card - high end, modern health care

Hey designers!

We need a double sided business card for the boutique, cutting edge physical therapy rehabilitation centre in Sydney's Northern Beaches.

With the most qualified physios in the area The Harbourview Motion Clinic does what other physiotherapy practices do not, we take our time with our patients giving them longer appointments, better physios and therefor faster results!

We guarantee that the service people receive at THMC will be unparalleled.

Hence we need a business card to reflect our modern, boutique, high end service. The final design needs to reflect that we are in a class of our own yet with the feel of beachside retreat.

Below I have attached our logo in both blue on white and white on blue. The exact colour is;
and the font that we have used in our logo is Tex Gyre Aventador.

I like the idea of the blue as the main colour as it is more eye catching and our signage onto the main road will be in this blue and in the interest of consistency across marketing the blue needs to be a part of the design. However I would appreciate a few designs onto a wooden background as this is a visual theme within the fitout of the practice.

The design needs to be of standard size (91x55mm).

Target Market(s)

We target people who have an end outcome in mind and those who have had poor experiences with other providers and ensure that everyone gets the care that they deserve with a premium service that is tailored to the individuals circumstances. As a premium service, the target market is highly educated, business and tech savvy with the additional target market of elderly people who have self funded their retirement and see value in paying for the best ongoing rehabilitation to maintain independence.

Industry/Entity Type

Physical Therapy

Contact Information for Business Card

Name, designation( Titled Musculoskeletal Physiotherapist... there will also be those in the company that have multiple designations ie 5 or 6 words long), phone number, email, facebook, instagram, address

Font styles to use
Sans Serif

Colors

Designer to choose colors to be used in the design.

Requirements
Must have
• Front - The logo as large as possible, blue or wooden theme, and all of the important details.
• Back - A blank space/lines on which to write appointment times (no "Appointment, date, time" etc.)
Nice to have
• facebook url
• logos for facebook and instagram
• Mini logos for the phone and email?

```html
<!DOCTYPE html>
<html lang="en">
<head>
<meta charset="utf-8">
<title>The Harbourview Motion Clinic – Business Card</title>
<link href="https://fonts.googleapis.com/css2?family=Raleway:wght@400;500;700&display=swap" rel="stylesheet">
<style>
  :root {
    --brand-blue: #0e57a8;
    --brand-blue-soft: rgba(255,255,255,0.12);
    --paper: #ffffff;
    --ink: #1d1d1f;
    --rule: #2b2b2b;
    --backdrop: #ddd6cd;
    --social-a: #1b8fd6;
    --social-b: #e9578f;
  }
  * { box-sizing: border-box; margin: 0; padding: 0; }
  html, body { width: 1200px; height: 1200px; overflow: hidden; }
  body {
    background: var(--backdrop);
    font-family: "Raleway", sans-serif;
    position: relative;
  }
  .card {
    position: absolute;
    border-radius: 40px;
    overflow: hidden;
    box-shadow: 0 10px 24px rgba(0,0,0,0.22);
  }
  /* Front */
  .card-front {
    left: 128px; top: 114px; width: 778px; height: 444px;
    background: var(--brand-blue);
  }
  .front-ring {
    position: absolute;
    left: 341px; top: 160px; width: 364px; height: 364px;
    border-radius: 50%;
    border: 28px solid var(--brand-blue-soft);
  }
  .front-brand {
    position: absolute;
    left: 50%; top: 50%;
    transform: translate(-50%, -50%);
    display: flex; align-items: center; gap: 14px;
    color: var(--paper);
    white-space: nowrap;
  }
  .brand-dot {
    width: 84px; height: 84px; border-radius: 50%;
    background: var(--paper);
    flex: none;
  }
  .brand-name { font-weight: 700; line-height: 1; text-transform: uppercase; }
  .front-brand .line-main { display: block; font-size: 40px; letter-spacing: 0.02em; }
  .front-brand .line-sub { display: block; font-size: 24px; letter-spacing: 0.7em; margin-top: 8px; }

  /* Back */
  .card-back {
    left: 292px; top: 632px; width: 778px; height: 446px;
    background: var(--paper);
    color: var(--ink);
  }
  .side-strip {
    position: absolute; left: 0; top: 0; width: 148px; height: 100%;
    border-right: 1.5px solid var(--rule);
  }
  .side-brand {
    position: absolute; left: 82px; top: 223px;
    transform: translate(-50%, -50%) rotate(-90deg);
    display: flex; align-items: center; gap: 10px;
    color: var(--brand-blue);
    white-space: nowrap;
  }
  .side-brand .brand-dot { width: 54px; height: 54px; background: var(--brand-blue); }
  .side-brand .line-main { display: block; font-size: 24px; letter-spacing: 0.02em; }
  .side-brand .line-sub { display: block; font-size: 14px; letter-spacing: 0.72em; margin-top: 5px; }

  .person { position: absolute; left: 178px; top: 86px; }
  .person-name { font-size: 30px; font-weight: 400; }
  .person-name .accent { color: var(--brand-blue); }
  .person-role { font-size: 18px; font-weight: 500; margin-top: 8px; }

  .rule { position: absolute; left: 148px; width: 568px; height: 1.5px; background: var(--rule); }
  .rule-top { top: 170px; }
  .rule-bottom { top: 342px; }

  .contact {
    position: absolute; left: 178px;
    display: flex; align-items: center; gap: 18px;
    font-size: 21px; font-weight: 500;
  }
  .contact svg { flex: none; }
  .contact-phone { top: 202px; }
  .contact-email { top: 240px; }

  .social {
    position: absolute; top: 298px;
    display: flex; align-items: center; gap: 12px;
    font-size: 18px; font-weight: 500;
  }
  .social-first { left: 178px; }
  .social-second { left: 446px; }
  .social-dot { width: 26px; height: 26px; border-radius: 50%; }
  .social-first .social-dot { background: var(--social-a); }
  .social-second .social-dot { background: var(--social-b); }

  .write-line {
    position: absolute; left: 185px; top: 400px; width: 531px;
    border-top: 1.5px dashed var(--rule);
  }
</style>
</head>
<body>

<section class="card card-front" aria-label="Card front">
  <div class="front-ring" aria-hidden="true" style="left:213px;top:46px;"></div>
  <div class="front-brand">
    <span class="brand-dot" aria-hidden="true"></span>
    <span class="brand-name">
      <span class="line-main">The Harbourview</span>
      <span class="line-sub">Motion Clinic</span>
    </span>
  </div>
</section>

<section class="card card-back" aria-label="Card back">
  <div class="side-strip">
    <div class="side-brand">
      <span class="brand-dot" aria-hidden="true"></span>
      <span class="brand-name">
        <span class="line-main">The Harbourview</span>
        <span class="line-sub">Motion Clinic</span>
      </span>
    </div>
  </div>

  <div class="person">
    <p class="person-name">Name of <span class="accent">Person</span></p>
    <p class="person-role">Designation</p>
  </div>

  <div class="rule rule-top"></div>

  <p class="contact contact-phone">
    <svg width="28" height="28" viewBox="0 0 28 28" aria-hidden="true">
      <circle cx="14" cy="14" r="12.5" fill="none" stroke="#1d1d1f" stroke-width="2"/>
      <path d="M10 7.5c-1.6 1-2 2.6-1.4 4.4 1.2 3.6 3.9 6.4 7.4 7.8 1.8.7 3.4.3 4.4-1.3l-2.5-2.2-1.8 1.1c-1.9-.9-3.3-2.4-4.2-4.3l1.1-1.8z" fill="#1d1d1f"/>
    </svg>
    <span>555.014.2290</span>
  </p>
  <p class="contact contact-email">
    <svg width="28" height="20" viewBox="0 0 28 20" aria-hidden="true">
      <rect x="0" y="1" width="28" height="18" fill="#1d1d1f"/>
      <path d="M1.5 2.5 14 12 26.5 2.5" fill="none" stroke="#fff" stroke-width="1.6"/>
      <path d="M1.5 18 10.5 9.5M26.5 18 17.5 9.5" stroke="#fff" stroke-width="1.6"/>
    </svg>
    <span>hello@harbourviewmotion.com</span>
  </p>

  <p class="social social-first"><span class="social-dot" aria-hidden="true"></span><span>harbourview.mc</span></p>
  <p class="social social-second"><span class="social-dot" aria-hidden="true"></span><span>@harbourview_mc</span></p>

  <div class="rule rule-bottom"></div>
  <div class="write-line" aria-hidden="true"></div>
</section>

</body>
</html>
```